Biz Cards to match new logo

I'm looking for a business card layout to go with my new logo. I'd like to have one side in colour (purple, with the logo in white) and the other side to be white with the purple logo and contact info in black font: name, address (2 lines), phone, email, fax, website. The logo includes the company name so it doesn't need to be repeated in the text. The font should be legibile to the semi-blind. (I hate small fonts on business cards).

Industry/Entity Type

Business

```html
<!DOCTYPE html>
<html lang="en">
<head>
<meta charset="utf-8">
<title>Meridian Research – Business Cards</title>
<link href="https://fonts.googleapis.com/css2?family=Questrial&display=swap" rel="stylesheet">
<style>
  :root {
    --purple: #6a3d8f;
    --purple-soft: #9a80b3;
    --paper: #ffffff;
    --ink: #1c1c1c;
    --backdrop: #f4f4f6;
    --card-w: 540px;
    --card-h: 309px;
  }
  * { box-sizing: border-box; margin: 0; padding: 0; }
  html, body {
    width: 1200px;
    height: 873px;
    overflow: hidden;
    background: var(--backdrop);
    font-family: "Questrial", "Century Gothic", sans-serif;
  }
  .canvas {
    position: relative;
    width: 1200px;
    height: 873px;
  }
  .card {
    position: absolute;
    top: 282px;
    width: var(--card-w);
    height: var(--card-h);
    overflow: hidden;
    box-shadow: 0 6px 18px rgba(0, 0, 0, 0.12);
  }
  .card--contact { left: 40px; background: var(--paper); }
  .card--brand { left: 620px; background: var(--purple); }

  .card__curve {
    position: absolute;
    inset: 0;
    width: 100%;
    height: 100%;
  }

  .brand-name {
    position: absolute;
    font-size: 27px;
    letter-spacing: 1px;
    text-transform: uppercase;
    line-height: 1.15;
    display: flex;
    align-items: center;
    gap: 10px;
  }
  .brand-name__mark {
    width: 18px;
    height: 18px;
    flex: none;
  }
  .card--contact .brand-name {
    left: 112px;
    top: 118px;
    width: 170px;
    color: var(--purple);
  }
  .card--contact .brand-name__mark { background: var(--purple); }

  .card--brand .brand-name {
    left: 0;
    right: 0;
    top: 0;
    bottom: 0;
    justify-content: center;
    color: var(--paper);
    font-size: 32px;
    letter-spacing: 2px;
  }
  .card--brand .brand-name__mark { background: var(--paper); }

  .contact {
    position: absolute;
    left: 300px;
    top: 62px;
    padding-left: 18px;
    border-left: 2px solid var(--purple);
    list-style: none;
    color: var(--ink);
    font-size: 21px;
    line-height: 1.22;
  }
  .contact__name {
    color: var(--purple);
    font-size: 22px;
    letter-spacing: 0.5px;
    margin-bottom: 6px;
  }
</style>
</head>
<body>
<main class="canvas">

  <section class="card card--contact" aria-label="Business card, contact side">
    <svg class="card__curve" viewBox="0 0 540 309" preserveAspectRatio="none" aria-hidden="true">
      <path d="M0 0 H46 Q112 154 46 309 H0 Z" fill="var(--purple-soft)"/>
      <path d="M0 0 H34 Q92 154 34 309 H0 Z" fill="var(--purple)"/>
    </svg>
    <div class="brand-name">
      <span class="brand-name__mark"></span>
      <span>Meridian Research</span>
    </div>
    <ul class="contact">
      <li class="contact__name">NAME</li>
      <li>Address line 1</li>
      <li>Address line 2</li>
      <li>Phone</li>
      <li>Email</li>
      <li>Fax</li>
      <li>Website</li>
    </ul>
  </section>

  <section class="card card--brand" aria-label="Business card, brand side">
    <div class="brand-name">
      <span class="brand-name__mark"></span>
      <span>Meridian Research</span>
    </div>
  </section>

</main>
</body>
</html>
```